shop signs for newquay all year round

We require a shop front signage
2 x 2.5m Long by 1.5m High (sides)
1 x 8m long by 0.7m High (front)

The front sign must read - Pennywell Bargain Store with the last 1.5m showing the the Xmas Shop open all year (see image 1)

The side signs must have a big bold Arrow pointing Left and one Pointing Right with the words Clearance Sale Now On (see image 2)

Colors

Designer to choose colors to be used in the design.

Requirements
Must have
• signs must be bold and clear to get shoppers into the store, it must be bright and stand out
Nice to have
• good graphics and artwork
Should not have
• plain text

```html
<!DOCTYPE html>
<html lang="en">
<head>
<meta charset="utf-8">
<title>Pennywell Bargain Store – Shop Front Signage</title>
<link rel="stylesheet" href="https://fonts.googleapis.com/css2?family=Montserrat:wght@500;600;800&family=Kaushan+Script&display=swap">
<style>
  :root {
    --backdrop: #e4e4e4;
    --red-deep: #9c1226;
    --red-mid: #c41636;
    --red-bright: #d01a3c;
    --white: #ffffff;
    --shadow: rgba(0, 0, 0, 0.35);
  }
  * { margin: 0; padding: 0; box-sizing: border-box; }
  html, body {
    width: 1200px;
    height: 1000px;
    overflow: hidden;
    background: var(--backdrop);
  }
  .signage {
    position: relative;
    width: 1200px;
    height: 1000px;
    font-family: "Montserrat", Arial, sans-serif;
    color: var(--white);
  }
  .sign-face {
    position: absolute;
    background: linear-gradient(90deg,
      var(--red-deep) 0%, var(--red-mid) 22%, var(--red-bright) 48%,
      var(--red-mid) 72%, var(--red-deep) 100%);
    box-shadow: 0 3px 8px var(--shadow);
  }
  .inner-frame {
    position: absolute;
    border: 1.5px solid rgba(255, 255, 255, 0.85);
  }

  /* Front fascia */
  .fascia { left: 57px; top: 204px; width: 1086px; height: 137px; }
  .fascia .inner-frame { left: 8px; top: 8px; width: 862px; height: 121px; }
  .store-name {
    position: absolute;
    left: 8px; top: 8px; width: 862px; height: 121px;
    display: flex; align-items: center; justify-content: center;
    font-weight: 500;
    font-size: 58px;
    letter-spacing: -0.5px;
  }
  .xmas-panel {
    position: absolute;
    left: 878px; top: 0; width: 208px; height: 137px;
    background: linear-gradient(90deg, var(--red-deep), var(--red-mid) 60%, var(--red-bright));
  }
  .xmas-decoration {
    position: absolute;
    right: 0; top: 0; width: 110px; height: 137px;
    background: radial-gradient(circle at 60% 75%, rgba(255,255,255,0.35), transparent 28%),
                radial-gradient(circle at 70% 25%, rgba(255,255,255,0.25), transparent 22%),
                radial-gradient(circle at 25% 55%, rgba(255,255,255,0.18), transparent 25%);
  }
  .xmas-title {
    position: absolute;
    left: 14px; top: 10px;
    font-family: "Kaushan Script", cursive;
    font-size: 30px;
    line-height: 36px;
    text-shadow: 1px 1px 2px var(--shadow);
  }
  .xmas-title span { display: block; }
  .xmas-title span + span { margin-left: 6px; }
  .xmas-note {
    position: absolute;
    left: 16px; top: 94px;
    font-weight: 600;
    font-size: 13px;
    line-height: 16px;
  }

  /* Side signs */
  .side-sign { top: 365px; width: 478px; height: 380px; }
  .side-sign--right-arrow { left: 62px; }
  .side-sign--left-arrow { left: 663px; }
  .side-sign .inner-frame { left: 11px; top: 11px; width: 456px; height: 358px; }
  .sale-heading {
    position: absolute;
    left: 0; top: 34px; width: 100%;
    text-align: center;
    font-weight: 800;
    font-size: 60px;
    line-height: 58px;
    letter-spacing: -1px;
    text-shadow: 3px 3px 3px var(--shadow);
  }
  .sale-status {
    position: absolute;
    left: 0; top: 178px; width: 100%;
    text-align: center;
    font-weight: 500;
    font-size: 43px;
    letter-spacing: -0.5px;
  }
  .direction-arrow {
    position: absolute;
    left: 102px; top: 246px;
    width: 274px; height: 102px;
    filter: drop-shadow(2px 2px 2px var(--shadow));
  }
</style>
</head>
<body>
<main class="signage">

  <section class="sign-face fascia" aria-label="Front fascia sign">
    <div class="inner-frame"></div>
    <h1 class="store-name">Pennywell Bargain Store</h1>
    <div class="xmas-panel">
      <div class="xmas-decoration" role="img" aria-label="Hanging Christmas baubles and snowflakes decoration"></div>
      <p class="xmas-title"><span>Christmas</span><span>Shop</span></p>
      <p class="xmas-note">OPEN<br>ALL YEAR</p>
    </div>
  </section>

  <section class="sign-face side-sign side-sign--right-arrow" aria-label="Side sign, arrow right">
    <div class="inner-frame"></div>
    <h2 class="sale-heading">CLEARANCE<br>SALE</h2>
    <p class="sale-status">NOW ON</p>
    <svg class="direction-arrow" viewBox="0 0 274 102" aria-hidden="true">
      <path fill="#fff" d="M6 26 H210 V6 Q210 0 216 4 L270 47 Q274 51 270 55 L216 98 Q210 102 210 96 V76 H6 Q0 76 0 70 V32 Q0 26 6 26 Z"/>
    </svg>
  </section>

  <section class="sign-face side-sign side-sign--left-arrow" aria-label="Side sign, arrow left">
    <div class="inner-frame"></div>
    <h2 class="sale-heading">CLEARANCE<br>SALE</h2>
    <p class="sale-status">NOW ON</p>
    <svg class="direction-arrow" viewBox="0 0 274 102" aria-hidden="true">
      <path fill="#fff" transform="translate(274 0) scale(-1 1)" d="M6 26 H210 V6 Q210 0 216 4 L270 47 Q274 51 270 55 L216 98 Q210 102 210 96 V76 H6 Q0 76 0 70 V32 Q0 26 6 26 Z"/>
    </svg>
  </section>

</main>
</body>
</html>
```